UI Improvement for FlorKeep app

We are looking for a talented UI/UX designer to REFINE and enhance the visual design of our mobile application, FlorKeep. The app is fully functional, but we need a designer to improve its aesthetics by specifying design elements such as fonts, colors, spacing, and component styles.
Your task will be to analyze the CURRENT UI and provide detailed design specifications that will make the app more visually appealing, modern, and user-friendly.
TODO:
Review the existing FlorKeep app design (see attachments) and identify areas for visual improvement.
Provide a detailed UI style guide, including:
Typography (font choices, sizes, and weights)
Color palette (primary, secondary, and accent colors)
Component styling (buttons, forms, icons, and interactive elements)
Spacing and layout guidelines (margins, paddings, and alignment)
Ensure the design remains clean, modern, and professional while maintaining usability and accessibility.
Provide design mockups or visual examples (if possible) to illustrate the proposed changes.
Deliverables:
A UI Style Guide (PDF or Figma file) with specifications on fonts, colors, spacing, and UI components.
Optionally, before/after mockups or examples demonstrating the improvements.
Ideal Designer:
Strong experience in mobile UI/UX design.
Understanding of modern design trends and best practices.
Ability to communicate design choices clearly for easy developer implementation.
I have attached 7 images showcasing the main UI screens used in the FlorKeep app. These screens need visual enhancements to improve their overall look and user experience.
The images represent the current design in three key modes:
LIST Mode – Displays data in a structured list format.
READ Mode – Shows detailed information when a user selects an item.
ADD/EDIT Mode – Allows users to input or modify information.
Additionally, there is a ‘MORE’ page, which serves as a menu listing other features of the application.
Task Objective:
Please refine and improve these UIs to create a more modern, visually appealing, and user-friendly experience. Focus on typography, colors, spacing, and component styling to ensure a cohesive and polished design.
Look and feel
Each slider illustrates characteristics of the customer's brand and the style your logo design should communicate.

```html
<!DOCTYPE html>
<html lang="en">
<head>
<meta charset="utf-8">
<title>FlorKeep – UI Screens</title>
<link href="https://fonts.googleapis.com/css2?family=Inter:wght@400;500;600;700&display=swap" rel="stylesheet">
<style>
:root{
  --bg:#e2e2e2;
  --blue:#1b5fc1;
  --blue-deep:#154ea3;
  --ink:#1f2430;
  --muted:#9aa1ad;
  --line:#e6e9ef;
  --surface:#f2f4f8;
  --card:#ffffff;
  --tint:#e3edfb;
  --icon:#8fb3e6;
  --green:#17a34a;
  --green-tint:#e2f6e8;
  --grey-tag:#eceef2;
  --yellow:#fcf7c2;
  --sky:#bfdff9;
  --mint:#bff4b9;
  --tab-dim:#4f8ee3;
}
*{box-sizing:border-box;margin:0;padding:0}
html,body{width:686px;height:1200px;overflow:hidden;background:var(--bg)}
body{font-family:'Inter',sans-serif;color:var(--ink)}
.board{position:absolute;left:0;top:0;width:1456px;height:2547px;transform:scale(.47115);transform-origin:0 0}
.caption{position:absolute;width:300px;text-align:center;font-weight:700;font-size:12px;letter-spacing:.2px;color:#222;line-height:26px}
.caption.sub{color:#888}
.pointer{position:absolute;left:855px;top:2237px;width:2px;height:28px;background:#222}

.screen{position:absolute;width:212px;border-radius:24px;overflow:hidden;background:var(--surface)}
.hdr{position:relative;height:76px;color:#fff}
.hdr.tall{height:108px}
.hdr-photo{position:absolute;inset:0;background:linear-gradient(180deg,#1a56b0 0%,#1f63c6 60%,#1b5fc1 100%)}
.status{position:absolute;top:12px;left:16px;right:16px;display:flex;justify-content:space-between;font-size:6px;font-weight:500}
.status i{width:22px;height:5px;border-radius:2px;background:rgba(255,255,255,.8)}
.titlebar{position:absolute;top:38px;left:12px;right:12px;height:16px;display:flex;align-items:center;justify-content:center}
.titlebar h1{font-size:11px;font-weight:600}
.titlebar.left{justify-content:flex-start}
.titlebar.left h1{margin-left:6px}
.back,.dots{position:absolute;width:12px;height:12px;border-radius:50%;background:rgba(255,255,255,.25)}
.back{left:0}.dots{right:0}
.back::after{content:"";position:absolute;left:4.5px;top:4px;width:3px;height:3px;border-left:1px solid #fff;border-bottom:1px solid #fff;transform:rotate(45deg)}
.dots::after{content:"···";position:absolute;inset:0;font-size:7px;line-height:11px;text-align:center}
.pill-btn{position:absolute;right:16px;height:12px;padding:0 8px;border-radius:8px;background:rgba(255,255,255,.3);font-size:5.5px;line-height:12px;font-weight:600}

.body{padding:8px 10px}
.sheet{background:var(--card);border-radius:10px;margin:-38px 10px 0;padding:10px 8px;position:relative}
.sec{display:flex;justify-content:space-between;align-items:center;font-size:8px;font-weight:500;padding:6px 4px 8px}
.sec .more{color:var(--muted);font-size:7px}
.chev{width:4px;height:4px;border-right:1px solid #556;border-bottom:1px solid #556;transform:rotate(45deg);flex:none}

.fld{position:relative;display:flex;align-items:center;gap:10px;height:32px;padding:0 10px;margin-bottom:8px;background:var(--card);border:1px solid var(--line);border-radius:5px}
.fld small{display:block;font-size:4.6px;color:var(--muted);margin-bottom:3px}
.fld b{display:block;font-size:7px;font-weight:500}
.fld .chev{position:absolute;right:12px;top:12px}
.fld .star{color:var(--blue);font-size:5px}
.ic{width:10px;height:10px;border:1px solid #a6adb8;border-radius:3px;flex:none}
.tinted .ic{width:14px;height:14px;border:none;border-radius:50%;background:var(--tint);box-shadow:inset 0 0 0 3px var(--tint),inset 0 0 0 5px var(--icon)}
.pair{display:flex;gap:8px}
.pair .fld{flex:1}

.nav{position:absolute;left:0;right:0;bottom:0;height:44px;background:var(--card);display:flex;align-items:center;justify-content:space-around;padding:0 14px}
.nav .nv{width:10px;height:10px;border-radius:3px;background:#bcd0ee}
.nav .active{height:18px;padding:0 9px;border-radius:10px;background:var(--blue);color:#fff;font-size:6px;font-weight:600;display:flex;align-items:center;gap:4px}
.nav .active::before{content:"";width:8px;height:8px;border-radius:2px;background:#fff}
.nav.blue{background:var(--blue);height:46px}
.nav.blue.labelled{align-items:flex-start;padding-top:10px}
.tab{display:flex;flex-direction:column;align-items:center;gap:3px;font-size:4.5px;color:var(--tab-dim)}
.tab::before{content:"";width:10px;height:10px;border-radius:3px;background:#3f86e6}
.tab.on{color:#fff}
.tab.on::before{background:#fff}
.nav.blue .active{background:#fff;color:var(--blue)}
.nav.blue .active::before{background:var(--blue)}
.nav.blue .nv{background:var(--tab-dim)}

.menu{background:var(--card);border-radius:10px;margin:10px 12px;padding:4px 8px}
.menu li{list-style:none;display:flex;align-items:center;gap:12px;height:29px;border-bottom:1px solid var(--line);font-size:6.5px}
.menu li:last-child{border:none}
.menu li i{width:10px;height:10px;border-radius:50%;background:var(--blue)}

.search{display:flex;align-items:center;justify-content:space-between;height:26px;background:var(--card);border-radius:6px;padding:0 8px;font-size:6.5px;margin-bottom:8px}
.search .filter{width:14px;height:14px;border-radius:50%;background:var(--blue)}
.search .glass{width:6px;height:6px;border:1px solid #aab;border-radius:50%}
.chips{display:flex;gap:6px;white-space:nowrap;font-size:5px;margin-bottom:8px;overflow:hidden}
.chips span{padding:2px 4px;border-radius:6px}
.chips .on{background:var(--blue);color:#fff}
.letter{display:flex;justify-content:space-between;align-items:center;font-size:8px;font-weight:500;padding:2px 4px 8px}

.entry{position:relative;display:flex;gap:10px;align-items:center;background:var(--card);border-radius:6px;padding:7px 8px;margin-bottom:6px}
.avatar{width:28px;height:28px;border-radius:50%;flex:none;background:radial-gradient(circle at 50% 40%,#6a8fbf,#1d2f4a)}
.entry h3{font-size:7px;font-weight:500;margin-bottom:5px}
.entry .date{position:absolute;right:8px;bottom:10px;font-size:5.5px;color:var(--muted)}
.tags{display:flex;gap:4px}
.tag{font-size:4.8px;padding:2px 5px;border-radius:6px;font-weight:500}
.tag.id{background:var(--tint);color:var(--blue)}
.tag.owner{color:var(--green)}
.tag.qual{color:var(--green);background:var(--green-tint)}
.tag.enth{color:var(--blue);background:var(--tint)}
.tag.pilot{background:var(--grey-tag);color:#444}

.actions{display:flex;gap:5px;margin:10px 8px}
.actions span{flex:1;height:17px;border-radius:4px;background:var(--card);font-size:5.5px;display:flex;align-items:center;justify-content:center;gap:3px}
.actions span::before{content:"";width:6px;height:6px;border-radius:2px;background:var(--blue)}
.actions .primary{background:var(--blue);color:#fff}
.actions .primary::before{background:#fff}
.readcard{background:var(--card);border-radius:8px;margin:0 8px 8px;padding:0 8px}
.rd{display:flex;gap:10px;align-items:center;padding:7px 0;border-bottom:1px solid var(--line)}
.rd:last-child{border:none}
.rd small{display:block;font-size:4.6px;color:var(--muted);margin-bottom:3px}
.rd b{display:block;font-size:7px;font-weight:500;line-height:1.45}
.rd .ic,.row .ic,.single .ic{width:14px;height:14px;border:none;border-radius:50%;background:var(--tint);box-shadow:inset 0 0 0 3.5px var(--tint),inset 0 0 0 5px var(--icon)}
.single{background:var(--card);border-radius:6px;margin:0 8px 8px;padding:8px;display:flex;gap:10px;align-items:center;font-size:7px}

.row{display:flex;align-items:center;gap:10px;height:28px;background:var(--card);border-radius:5px;padding:0 10px;margin-bottom:8px;font-size:7px}
.panel{border-radius:6px;padding:8px 6px;margin-bottom:8px;font-size:7px}
.panel.yellow{background:var(--yellow)}
.panel.sky{background:var(--sky)}
.panel.mint{background:var(--mint)}
.panel p{margin-bottom:8px}
.select{position:relative;background:var(--card);border-radius:5px;padding:7px 18px 7px 8px;font-size:6.2px;line-height:1.6}
.select .chev{position:absolute;right:8px;top:50%;margin-top:-3px}
.btn{margin-top:6px;height:11px;border-radius:6px;background:var(--blue-deep);color:#fff;font-size:5.5px;font-weight:600;line-height:11px;text-align:center}
.btn.inline{display:inline-block;padding:0 6px}
.dim{background:var(--card);border-radius:8px;padding:6px;margin:0 8px 8px}
.dim .select{background:var(--surface);margin-bottom:6px}
</style>
</head>
<body>
<div class="board">

  <div class="caption" style="left:90px;top:106px">ADD ACCOUNT</div>
  <div class="caption sub" style="left:94px;top:132px">RADS_ADDEDIT_PAGE</div>
  <div class="caption" style="left:373px;top:106px">ADD ACCOUNT - OPTION ONE</div>
  <div class="caption" style="left:683px;top:106px">ADD ACCOUNT - OPTION TWO</div>
  <div class="caption" style="left:1050px;top:98px">MORE</div>
  <div class="caption" style="left:1050px;top:117px">RADS_MORE_PAGE</div>

  <div class="caption" style="left:86px;top:804px">PILOTS</div>
  <div class="caption" style="left:82px;top:830px">RADS_LIST_PAGE1</div>
  <div class="caption" style="left:404px;top:804px">CONTACTS</div>
  <div class="caption" style="left:406px;top:830px">RADS_LISTPAGE2</div>
  <div class="caption" style="left:700px;top:804px">CONTACTS</div>
  <div class="caption" style="left:702px;top:830px">SEARCH RESULTS</div>
  <div class="caption" style="left:1049px;top:774px">PILOT DETAILS</div>
  <div class="caption" style="left:1047px;top:800px">RADS_READ_PAGE2</div>

  <div class="caption" style="left:90px;top:1579px">CONTACTS</div>
  <div class="caption" style="left:94px;top:1604px">RADS_READ_PAGE</div>
  <div class="caption" style="left:406px;top:1579px">CONTACTS</div>
  <div class="caption" style="left:413px;top:1604px">RADS_READ_PAGE2</div>
  <div class="caption" style="left:731px;top:1579px">PILOT DETAILS</div>
  <div class="caption" style="left:729px;top:1604px">RADS_READ_PAGE2</div>
  <div class="pointer"></div>
  <div class="caption" style="left:715px;top:2264px">ADDED MENU NAME BELOW</div>

  <!-- Add account -->
  <section class="screen" style="left:140px;top:178px;height:552px">
    <div class="hdr tall"><div class="hdr-photo" role="img" aria-label="Blue-toned photo of an aircraft in flight"></div>
      <div class="status"><span>12:30PM</span><i></i></div>
      <div class="titlebar"><span class="back"></span><h1>Add Contact</h1><span class="pill-btn">Save</span><span class="dots"></span></div>
    </div>
    <div class="sheet">
      <div class="sec" style="padding-top:0">Contact Information <span class="more">···</span></div>
      <div class="fld"><i class="ic"></i><div><small>Business Name - e</small><b>Contact Business name</b></div></div>
      <div class="fld"><i class="ic"></i><div><small>First Name -e</small><b>Marcus</b></div></div>
      <div class="fld"><i class="ic"></i><div><small>Middle Name -e</small><b>Peter</b></div></div>
      <div class="fld"><i class="ic"></i><div><small>Last Name -e</small><b>Jennings</b></div></div>
      <div class="sec">Address Information <span class="chev"></span></div>
      <div class="fld"><i class="ic"></i><div><small>Address Label Tag -e</small><b>Address</b></div><span class="chev"></span></div>
      <div class="fld"><i class="ic"></i><div><small>Address Line1 -e <span class="star">★</span></small><b>Marcus</b></div></div>
      <div class="fld"><i class="ic"></i><div><small>Address Line2 -e <span class="star">★</span></small><b>Peter</b></div></div>
      <div class="fld"><i class="ic"></i><div><small>Address City</small><b>New York City, NY</b></div></div>
      <div class="pair"><div class="fld"><div><small>AddressState</small><b>New York</b></div><span class="chev"></span></div><div class="fld"><div><small>Zip -e</small><b>10021</b></div></div></div>
    </div>
    <nav class="nav"><span class="active">Contact</span><span class="nv"></span><span class="nv"></span><span class="nv"></span><span class="nv"></span></nav>
  </section>

  <!-- Option one -->
  <section class="screen" style="left:437px;top:178px;height:552px">
    <div class="hdr"><div class="hdr-photo" role="img" aria-label="Blue-toned photo of an aircraft in flight"></div>
      <div class="status"><span>12:30PM</span><i></i></div>
      <div class="titlebar"><span class="back"></span><h1>Add Contact</h1><span class="pill-btn">Save</span><span class="dots"></span></div>
    </div>
    <div class="body">
      <div class="sec">Contact Information <span class="more">···</span></div>
      <div class="fld"><i class="ic"></i><div><small>Business Name - e</small><b>Contact Business name</b></div></div>
      <div class="fld"><i class="ic"></i><div><small>First Name -e</small><b>Marcus</b></div></div>
      <div class="fld"><i class="ic"></i><div><small>Middle Name -e</small><b>Peter</b></div></div>
      <div class="fld"><i class="ic"></i><div><small>Last Name -e</small><b>Jennings</b></div></div>
      <div class="sec">Address Information <span class="chev"></span></div>
      <div class="fld"><i class="ic"></i><div><small>Address Label Tag -e</small><b>Address</b></div><span class="chev"></span></div>
      <div class="fld"><i class="ic"></i><div><small>Address Line1 -e <span class="star">★</span></small><b>Marcus</b></div></div>
      <div class="fld"><i class="ic"></i><div><small>Address Line2 -e <span class="star">★</span></small><b>Peter</b></div></div>
      <div class="fld"><i class="ic"></i><div><small>Address City</small><b>New York City, NY</b></div></div>
      <div class="pair"><div class="fld"><i class="ic"></i><div><small>AddressState</small><b>New York</b></div><span class="chev"></span></div><div class="fld"><i class="ic"></i><div><small>Zip -e</small><b>10021</b></div></div></div>
    </div>
    <nav class="nav"><span class="active">Contact</span><span class="nv"></span><span class="nv"></span><span class="nv"></span><span class="nv"></span></nav>
  </section>

  <!-- Option two -->
  <section class="screen tinted" style="left:737px;top:178px;height:560px">
    <div class="hdr"><div class="hdr-photo" role="img" aria-label="Blue-toned photo of an aircraft in flight"></div>
      <div class="status"><span>12:30PM</span><i></i></div>
      <div class="titlebar"><span class="back"></span><h1>Add Contact</h1><span class="pill-btn">Save</span><span class="dots"></span></div>
    </div>
    <div class="body">
      <div class="sec">Contact Information <span class="more">···</span></div>
      <div class="fld"><i class="ic"></i><div><small>Business Name - e</small><b>Contact Business name</b></div></div>
      <div class="fld"><i class="ic"></i><div><small>First Name -e</small><b>Marcus</b></div></div>
      <div class="fld"><i class="ic"></i><div><small>Middle Name -e</small><b>Peter</b></div></div>
      <div class="fld"><i class="ic"></i><div><small>Last Name -e</small><b>Jennings</b></div></div>
      <div class="sec">Address Information <span class="chev"></span></div>
      <div class="fld"><i class="ic"></i><div><small>Address Label Tag -e</small><b>Address</b></div><span class="chev"></span></div>
      <div class="fld"><i class="ic"></i><div><small>Address Line1 -e <span class="star">★</span></small><b>123 Main Street</b></div></div>
      <div class="fld"><i class="ic"></i><div><small>Address Line2 -e <span class="star">★</span></small><b>456 Elm Street, Apt 101</b></div></div>
      <div class="fld"><i class="ic"></i><div><small>Address City</small><b>New York City, NY</b></div></div>
      <div class="pair"><div class="fld"><div><small>AddressState</small><b>New York</b></div><span class="chev"></span></div><div class="fld"><div><small>Zip -e</small><b>10021</b></div></div></div>
    </div>
    <nav class="nav"><span class="active">Contact</span><span class="nv"></span><span class="nv"></span><span class="nv"></span><span class="nv"></span></nav>
  </section>

  <!-- More -->
  <section class="screen" style="left:1089px;top:178px;height:436px">
    <div class="hdr"><div class="hdr-photo" role="img" aria-label="Blue-toned photo of an aircraft in flight"></div>
      <div class="status"><span>12:30PM</span><i></i></div>
      <div class="titlebar left"><h1>More</h1><span class="dots"></span></div>
    </div>
    <ul class="menu">
      <li><i></i>Flight</li><li><i></i>Login</li><li><i></i>Account</li><li><i></i>Calendar</li><li><i></i>Users</li>
      <li><i></i>Dashboard</li><li><i></i>Tracking</li><li><i></i>Outreach Event</li><li><i></i>Maintenance Resource</li><li><i></i>Setting</li>
    </ul>
    <nav class="nav"><span class="nv"></span><span class="nv"></span><span class="nv"></span><span class="nv"></span><span class="active">More</span></nav>
  </section>

  <!-- Pilots list -->
  <section class="screen" style="left:129px;top:880px;height:562px">
    <div class="hdr"><div class="hdr-photo" role="img" aria-label="Blue-toned photo of pilots in uniform"></div>
      <div class="status"><span>12:30PM</span><i></i></div>
      <div class="titlebar"><span class="back"></span><h1>Pilots</h1><span class="pill-btn">Add</span><span class="dots"></span></div>
    </div>
    <div class="body">
      <div class="search"><span>Search</span><span class="filter"></span></div>
      <div class="letter">A <span class="chev"></span></div>
      <div class="entry"><span class="avatar" role="img" aria-label="Pilot portrait"></span><div><h3>Avery, Conrad Blake</h3><div class="tags"><span class="tag id">3182133</span></div></div><span class="date">9/30/24</span></div>
      <div class="entry"><span class="avatar" role="img" aria-label="Pilot portrait"></span><div><h3>Ashdown, Rowan Sterling</h3><div class="tags"><span class="tag id">4467155</span></div></div><span class="date">5/19/24</span></div>
      <div class="entry"><span class="avatar" role="img" aria-label="Pilot portrait"></span><div><h3>Amaro, Elsa, Noelle</h3><div class="tags"><span class="tag id">4360575</span></div></div><span class="date">2/25/25</span></div>
      <div class="letter">B <span class="chev"></span></div>
      <div class="entry"><span class="avatar" role="img" aria-label="Pilot portrait"></span><div><h3>Brightwell, Aidan, Hugo</h3><div class="tags"><span class="tag id">4360575</span></div></div><span class="date">9/30/24</span></div>
      <div class="entry"><span class="avatar" role="img" aria-label="Pilot portrait"></span><div><h3>Bramley, Reuben</h3><div class="tags"><span class="tag id">3423819</span></div></div><span class="date">2/28/25</span></div>
      <div class="letter">C <span class="chev"></span></div>
      <div class="entry"><span class="avatar" role="img" aria-label="Pilot portrait"></span><div><h3>Corwin, Dale, Yarrow</h3><div class="tags"><span class="tag id">2654896</span></div></div><span class="date">9/30/24</span></div>
    </div>
    <nav class="nav"><span class="nv"></span><span class="active">Pilot</span><span class="nv"></span><span class="nv"></span><span class="nv"></span></nav>
  </section>

  <!-- Contacts list -->
  <section class="screen" style="left:443px;top:880px;height:615px">
    <div class="hdr"><div class="hdr-photo" role="img" aria-label="Blue-toned photo of pilots in uniform"></div>
      <div class="status"><span>12:30PM</span><i></i></div>
      <div class="titlebar"><span class="back"></span><h1>Contacts</h1><span class="pill-btn">Add</span><span class="dots"></span></div>
    </div>
    <div class="body">
      <div class="search"><span>Search</span><span class="glass"></span></div>
      <div class="chips"><span class="on">All</span><span>Aircraft Owner</span><span>Enthusiast -e</span><span>Pilot</span><span>Flight S</span></div>
      <div class="entry"><span class="avatar" role="img" aria-label="Contact portrait"></span><div><h3>Avery, Conrad Blake</h3><div class="tags"><span class="tag owner">Aircraft Owner</span><span class="tag enth">Enthusiast -e</span></div></div></div>
      <div class="entry"><span class="avatar" role="img" aria-label="Contact portrait"></span><div><h3>Ashdown, Rowan Sterling</h3><div class="tags"><span class="tag owner">Aircraft Owner</span><span class="tag qual">Qualified Pilot</span><span class="tag pilot">Pilot</span></div></div></div>
      <div class="entry"><span class="avatar" role="img" aria-label="Contact portrait"></span><div><h3>Brightwell, Aidan, Hugo</h3><div class="tags"><span class="tag pilot">Pilot</span></div></div><span class="date">9/30/24</span></div>
      <div class="entry"><span class="avatar" role="img" aria-label="Contact portrait"></span><div><h3>Corwin, Dale, Yarrow</h3><div class="tags"><span class="tag owner">Aircraft Owner</span><span class="tag qual">Qualified Pilot</span><span class="tag pilot">Pilot</span></div></div></div>
      <div class="entry"><span class="avatar" role="img" aria-label="Contact portrait"></span><div><h3>Gresham, Jonah, Ellis</h3><div class="tags"><span class="tag owner">Aircraft Owner</span><span class="tag qual">Qualified Pilot</span><span class="tag pilot">Pilot</span></div></div></div>
      <div class="entry"><span class="avatar" role="img" aria-label="Contact portrait"></span><div><h3>Bramley, Reuben</h3><div class="tags"><span class="tag pilot">Pilot</span></div></div><span class="date">2/28/25</span></div>
      <div class="entry"><span class="avatar" role="img" aria-label="Contact portrait"></span><div><h3>Amaro, Elsa, Noelle</h3><div class="tags"><span class="tag owner">Aircraft Owner</span><span class="tag qual">Qualified Pilot</span></div></div></div>
    </div>
    <nav class="nav" style="bottom:70px;background:transparent"><span class="active">Contact</span><span class="nv"></span><span class="nv"></span><span class="nv"></span><span class="nv"></span></nav>
  </section>

  <!-- Contacts search -->
  <section class="screen" style="left:746px;top:880px;height:488px">
    <div class="hdr"><div class="hdr-photo" role="img" aria-label="Blue-toned photo of pilots in uniform"></div>
      <div class="status"><span>12:30PM</span><i></i></div>
      <div class="titlebar"><span class="back"></span><h1>Contacts</h1><span class="pill-btn">Add</span><span class="dots"></span></div>
    </div>
    <div class="body">
      <div class="search"><span>Search</span><span class="glass"></span></div>
      <div class="chips"><span class="on">All</span><span>Aircraft Owner</span><span>Enthusiast -e</span><span>Pilot</span><span>Fligh</span></div>
      <div class="entry"><span class="avatar" role="img" aria-label="Contact portrait"></span><div><h3>Avery, Conrad Blake</h3><div class="tags"><span class="tag owner">Aircraft Owner</span><span class="tag enth">Enthusiast -e</span></div></div></div>
      <div class="entry"><span class="avatar" role="img" aria-label="Contact portrait"></span><div><h3>Ashdown, Rowan Sterling</h3><div class="tags"><span class="tag owner">Aircraft Owner</span><span class="tag qual">Qualified Pilot</span><span class="tag pilot">Pilot</span></div></div></div>
      <div class="entry"><span class="avatar" role="img" aria-label="Contact portrait"></span><div><h3>Amaro, Elsa, Noelle</h3><div class="tags"><span class="tag owner">Aircraft Owner</span><span class="tag qual">Qualified Pilot</span></div></div></div>
      <div class="entry"><span class="avatar" role="img" aria-label="Contact portrait"></span><div><h3>Corwin, Dale, Yarrow</h3><div class="tags"><span class="tag owner">Aircraft Owner</span><span class="tag qual">Qualified Pilot</span><span class="tag pilot">Pilot</span></div></div></div>
      <div class="entry"><span class="avatar" role="img" aria-label="Contact portrait"></span><div><h3>Gresham, Jonah, Ellis</h3><div class="tags"><span class="tag owner">Aircraft Owner</span><span class="tag qual">Qualified Pilot</span><span class="tag pilot">Pilot</span></div></div></div>
    </div>
    <nav class="nav"><span class="active">Contact</span><span class="nv"></span><span class="nv"></span><span class="nv"></span><span class="nv"></span></nav>
  </section>

  <!-- Work order -->
  <section class="screen" style="left:1078px;top:850px;height:585px">
    <div class="hdr"><div class="hdr-photo" role="img" aria-label="Blue-toned photo of pilots in uniform"></div>
      <div class="status"><span>12:30PM</span><i></i></div>
      <div class="titlebar"><span class="back"></span><h1>Work Order</h1><span class="dots"></span></div>
    </div>
    <div class="actions"><span class="primary">Print</span><span>Create Name</span><span>Create Name</span></div>
    <div class="readcard">
      <div class="rd"><i class="ic"></i><div><small>Customer - e</small><b>Avery, Conrad, Blake</b></div></div>
      <div class="rd"><i class="ic"></i><div><small>Service Location -e</small><b>Billing, 418 Harbor Vale Rd, Lakemont tx, 70412</b></div></div>
      <div class="rd"><i class="ic"></i><div><small>Billing Address -e</small><b>Billing, 418 Harbor Vale Rd, Lakemont tx, 70412</b></div></div>
      <div class="rd"><i class="ic"></i><div><small>Description -e</small><b>Pool maintenance</b></div></div>
      <div class="rd"><i class="ic"></i><div><small>Work order type -e</small><b>One off job -e</b></div></div>
      <div class="rd"><i class="ic"></i><div><small>WO Status -e</small><b>Active -e</b></div></div>
      <div class="rd"><i class="ic"></i><div><small>Billing Frequency -e</small><b>Upon job completion -e</b></div></div>
    </div>
    <div class="single"><i class="ic"></i>Add Technician -e</div>
    <div class="single"><i class="ic"></i>Add Line Items -e</div>
    <nav class="nav blue labelled"><span class="tab">Contact</span><span class="tab on">Pilot</span><span class="tab">Plane</span><span class="tab">Fit Request</span><span class="tab">More</span></nav>
  </section>

  <!-- Contact read -->
  <section class="screen" style="left:129px;top:1654px;height:546px">
    <div class="hdr"><div class="hdr-photo" role="img" aria-label="Blue-toned photo of an aircraft in flight"></div>
      <div class="status"><span>12:30PM</span><i></i></div>
      <div class="titlebar"><span class="back"></span><h1>Contact</h1><span class="dots"></span></div>
    </div>
    <div class="body">
      <div class="row"><i class="ic"></i>Add Personal Information -e</div>
      <div class="row"><i class="ic"></i>Add Work Info -e</div>
      <div class="row"><i class="ic"></i>Add Skills/Talents -e</div>
      <div class="row"><i class="ic"></i>Add Resources -e</div>
      <div class="panel yellow"><p>Pilots -e</p><div class="select">Aldane, Curtis, 3647946, 10/31/23<span class="chev"></span></div></div>
      <div class="panel sky"><p>Aircraft Owner -e</p><div class="select">Aldane, Curtis: Aerolite: 18T: Aerolite Aircraft Company, Single Engine, 1100<span class="chev"></span></div><span class="btn inline">Add Aircraft Owner</span></div>
      <div class="panel mint"><p>Qualified Pilot -e</p><div class="select">Aldane, Curtis: Aerolite: 18T: Aerolite Aircraft Company, Single Engine, 1100<span class="chev"></span></div><span class="btn inline">Add Qualified Pilot -e</span></div>
    </div>
    <nav class="nav blue"><span class="active">Contact</span><span class="nv"></span><span class="nv"></span><span class="nv"></span><span class="nv"></span></nav>
  </section>

  <!-- Contact read 2 -->
  <section class="screen" style="left:444px;top:1654px;height:636px">
    <div class="hdr"><div class="hdr-photo" role="img" aria-label="Blue-toned photo of an aircraft in flight"></div>
      <div class="status"><span>12:30PM</span><i></i></div>
      <div class="titlebar"><span class="back"></span><h1>Contact</h1><span class="dots"></span></div>
    </div>
    <div class="body">
      <div class="row"><i class="ic"></i>Add Email -e</div>
      <div class="row"><i class="ic"></i>Add Social Media -e</div>
      <div class="row"><i class="ic"></i>Add Emergency Contact -e</div>
      <div class="row"><i class="ic"></i>Add Personal Information -e</div>
      <div class="row"><i class="ic"></i>Add Work Info -e</div>
      <div class="row"><i class="ic"></i>Add Skills/Talents -e</div>
      <div class="row"><i class="ic"></i>Add Resources -e</div>
      <div class="panel yellow"><p>Pilots -e</p><div class="select">Aldane, Curtis, 3647946, 10/31/23<span class="chev"></span></div></div>
      <div class="panel sky"><p>Aircraft Owner -e</p><div class="select">Aldane, Curtis: Aerolite: 18T: Aerolite Aircraft Company, Single Engine, 1100<span class="chev"></span></div><div class="btn">Add Aircraft Owner</div></div>
      <div class="panel mint"><p>Qualified Pilot -e</p><div class="select">Aldane, Curtis: Aerolite: 18T: Aerolite Aircraft Company, Single Engine, 1100<span class="chev"></span></div><div class="btn">Add Qualified Pilot -e</div></div>
    </div>
    <nav class="nav blue"><span class="active">Contact</span><span class="nv"></span><span class="nv"></span><span class="nv"></span><span class="nv"></span></nav>
  </section>

  <!-- Pilot read -->
  <section class="screen" style="left:760px;top:1654px;height:581px">
    <div class="hdr"><div class="hdr-photo" role="img" aria-label="Blue-toned photo of pilots in uniform"></div>
      <div class="status"><span>12:30PM</span><i></i></div>
      <div class="titlebar"><span class="back"></span><h1>Pilot</h1><span class="dots"></span></div>
    </div>
    <div class="readcard" style="margin-top:8px">
      <div class="rd"><i class="ic"></i><div><small>Pilot - e</small><b>Avery, Conrad, Blake</b></div></div>
      <div class="rd"><i class="ic"></i><div><small>Pilot Certificate No -e</small><b>3182133</b></div></div>
      <div class="rd"><i class="ic"></i><div><small>Medical Expiration Date -e</small><b>9/30/24</b></div></div>
      <div class="rd"><i class="ic"></i><div><small>Flight Review Expiration Date -e</small><b>6/30/24</b></div></div>
      <div class="rd"><i class="ic"></i><div><small>Total Flight Time -e</small><b>2500</b></div></div>
    </div>
    <div class="dim">
      <div class="select">Aldane, Curtis: Aerolite: 18T: Aerolite Aircraft Company, Single Engine, 1100<span class="chev"></span></div>
      <div class="select">Aldane, Curtis: Aerolite: 18T: Aerolite Aircraft Company, Single Engine, 1100<span class="chev"></span></div>
      <div class="btn">Add Base Airport -e</div>
    </div>
    <div class="single"><i class="ic"></i>Add Ratings -s</div>
    <div class="readcard">
      <div class="rd"><i class="ic"></i><div><small>Contact -e</small><b>Dana Whitfield</b></div></div>
      <div class="rd"><i class="ic"></i><div><small>Phone -e</small><b>555-014-2290</b></div></div>
      <div class="rd"><i class="ic"></i><div><small>Medical Expiration Date -e</small><b>9/30/24</b></div></div>
    </div>
    <nav class="nav blue labelled"><span class="tab">Contact</span><span class="tab on">Pilot</span><span class="tab">Plane</span><span class="tab">Fit Request</span><span class="tab">More</span></nav>
  </section>

</div>
</body>
</html>
```